Fabric Store Business card

Need a business card portraying store logo and up and coming business of quilt fabrics, apparel fabrics, notions and buttons. Our business name is Gilded Thimble and Beyond. Am attaching logo. The design should communicate a growing business and warm atmosphere. Would like address and store hours and contact info displayed on card. Mon - Fri 9:30 to 5:00, Saturday 9:30 to 1:00. Address 784 W Orchard Ave, Newton, KS 67230 email: gildedthimblebeyond@mailvexa.com. Phone and fax 316-527-3486. After hours contact # 620-431-9052 Also like vintage sewing machines and dress forms if it works to incorporate fine, if not thats ok too.
Store

```html
<!DOCTYPE html>
<html lang="en">
<head>
<meta charset="utf-8">
<title>Gilded Thimble and Beyond – Business Card</title>
<link rel="stylesheet" href="https://fonts.googleapis.com/css2?family=Open+Sans:wght@400;600&display=swap">
<style>
  :root {
    --backdrop: #e9e5df;
    --ink-black: #1d1d1f;
    --card-white: #ffffff;
    --thread-red: #9b1c24;
    --text-light: #f2f2f2;
    --divider-grey: #8a8a8a;
    --faint-shape: #262628;
  }
  html, body {
    margin: 0;
    padding: 0;
    overflow: hidden;
  }
  body {
    width: 1200px;
    height: 784px;
    background: var(--backdrop);
    font-family: "Open Sans", Arial, sans-serif;
    display: flex;
    align-items: center;
    justify-content: center;
    gap: 40px;
  }
  .card {
    position: relative;
    width: 540px;
    height: 309px;
    overflow: hidden;
    box-shadow: 0 6px 18px rgba(0,0,0,0.18);
  }
  .card-back { background: var(--ink-black); }
  .card-front { background: var(--card-white); }
  .card-shape {
    position: absolute;
    inset: 0;
  }
  .decor-area {
    position: absolute;
    right: 30px;
    top: 40px;
    width: 170px;
    height: 220px;
    border-radius: 80px 80px 20px 20px;
    background: radial-gradient(ellipse at center, #2b2b2e 0%, var(--faint-shape) 60%, var(--ink-black) 100%);
  }
  .brand {
    position: absolute;
    display: flex;
    align-items: center;
    gap: 12px;
  }
  .brand-dot {
    width: 46px;
    height: 46px;
    border-radius: 50%;
    background: var(--thread-red);
    flex: none;
  }
  .brand-name {
    font-size: 23px;
    font-weight: 400;
    letter-spacing: 0.3px;
    white-space: nowrap;
  }
  .card-back .brand { left: 70px; top: 92px; }
  .card-back .brand-name { color: var(--text-light); }
  .card-front .brand { left: 40px; top: 48px; }
  .card-front .brand-name { color: var(--thread-red); }
  .store-hours {
    position: absolute;
    left: 34px;
    top: 222px;
    margin: 0;
    color: var(--thread-red);
    font-size: 14px;
    line-height: 1.35;
    text-align: right;
    width: 150px;
  }
  .contact-divider {
    position: absolute;
    left: 196px;
    top: 186px;
    width: 1px;
    height: 86px;
    background: var(--divider-grey);
  }
  .contact-list {
    position: absolute;
    left: 206px;
    top: 184px;
    margin: 0;
    padding: 0;
    list-style: none;
    font-size: 11.5px;
    line-height: 1.55;
    color: var(--text-light);
  }
  .contact-label { color: var(--thread-red); }
</style>
</head>
<body>
  <section class="card card-back" aria-label="Card back">
    <div class="decor-area" role="img" aria-label="Faint vintage dress form and sewing machine decoration"></div>
    <div class="brand">
      <span class="brand-dot"></span>
      <span class="brand-name">Gilded Thimble and Beyond</span>
    </div>
  </section>

  <section class="card card-front" aria-label="Card front">
    <svg class="card-shape" width="540" height="309" viewBox="0 0 540 309" aria-hidden="true">
      <path d="M540,0 C470,90 360,135 240,162 C380,145 480,95 540,40 Z" fill="var(--thread-red)"/>
      <path d="M540,30 C450,120 300,160 0,185 L0,309 L540,309 Z" fill="var(--ink-black)"/>
    </svg>
    <div class="brand">
      <span class="brand-dot"></span>
      <span class="brand-name">Gilded Thimble and Beyond</span>
    </div>
    <p class="store-hours">Mon - Fri 9:30 to 5:00<br>Saturday 9:30 to 1:00</p>
    <span class="contact-divider"></span>
    <ul class="contact-list">
      <li>784 W Orchard Ave, Newton, KS 67230</li>
      <li><span class="contact-label">email:</span> gildedthimblebeyond@mailvexa.com</li>
      <li><span class="contact-label">Phone and fax:</span> 316-527-3486.</li>
      <li><span class="contact-label">After hours contact :</span> 620-431-9052</li>
    </ul>
  </section>
</body>
</html>
```